6 Posters - Outdoor Advertising

I need 6 posters, all with similar appearances but different texts, they need to draw attention to Dental professionals arriving at an event location.

All posters have different texts to be found in this document:
https://files.quorvexa.com/doc/7hRwqlmzTpa4KdvYbNcEe83XzQuLfgJsWoyVa2Bn/view

Goal is to have dental professionals visit the website clinivantagelab.com

Tech requirements Poster:
- 400 DPI
- Width: 118,5 cm / 46.65 inch of which 116 cm / 45.67 inch is visible
- Height: 175 cm / 68.90 inch of which 171 cm / 67.32 inch is visible

Target Market(s)

Dental Professionals

Industry/Entity Type

Dental

Font styles to use
Serif
Sans Serif

Colors

Designer to choose colors to be used in the design.

Requirements
Must have
• Attraction to cars driving approx 30 km/h / 20 miles/h
• Website: Clinivantagelab.com
• Logo
• Texts provided in https://files.quorvexa.com/doc/7hRwqlmzTpa4KdvYbNcEe83XzQuLfgJsWoyVa2Bn/view
Nice to have
• Picture(s) which are reminiscent of dentistry and customer satisfaction

```html
<!DOCTYPE html>
<html lang="nl">
<head>
<meta charset="utf-8">
<title>Clinivantage Lab – Posters</title>
<link rel="stylesheet" href="https://fonts.googleapis.com/css2?family=Montserrat:wght@400;500;600;700;800&family=Oswald:wght@500;600&family=Poppins:wght@300;400;500&display=swap">
<style>
:root{
  --bg:#bdbcc0;
  --paper:#ffffff;
  --blue:#2a6cc0;
  --blue-deep:#1f5aa6;
  --sky:#3a8fdc;
  --teal:#2f8f7b;
  --teal-soft:#3aa18a;
  --ink:#2b3440;
}
*{box-sizing:border-box;margin:0;padding:0}
html,body{width:1200px;height:1200px;overflow:hidden;background:var(--bg)}
body{position:relative;font-family:"Poppins",sans-serif}
.poster{position:absolute;width:334px;height:472px;background:var(--paper);overflow:hidden;box-shadow:0 6px 10px rgba(0,0,0,.28)}
.p1{left:55px;top:110px}.p2{left:436px;top:110px;background:linear-gradient(180deg,#2f86d6,#1f66bb)}.p3{left:817px;top:110px}
.p4{left:52px;top:618px}.p5{left:434px;top:618px}.p6{left:814px;top:618px}
.brand{position:absolute;left:0;right:0;display:flex;justify-content:center;align-items:center;gap:7px;
  font-family:"Montserrat",sans-serif;font-weight:700;color:var(--blue);letter-spacing:.5px;white-space:nowrap}
.brand .dot{border-radius:50%;background:var(--teal)}
.brand.lg{top:92px;font-size:18px}.brand.lg .dot{width:14px;height:14px}
.brand.md{top:76px;font-size:16px}.brand.md .dot{width:12px;height:12px}
.brand.sm{top:52px;font-size:13px}.brand.sm .dot{width:10px;height:10px}
.p2 .brand{color:#fff}.p2 .brand .dot{background:#fff}
.photo{position:absolute;left:0;right:0}
.band{position:absolute;left:0;right:0;top:430px;height:15px;background:var(--blue);color:#fff;
  font-family:"Montserrat",sans-serif;font-size:10.5px;letter-spacing:3.4px;text-align:center;line-height:15px;white-space:nowrap}
.p2 .band{background:#fff;color:var(--blue)}
.center{position:absolute;left:0;right:0;text-align:center;white-space:nowrap}
.cond{font-family:"Oswald",sans-serif;font-weight:600;text-transform:uppercase}
/* poster 1 */
.p1 .photo{top:146px;height:208px;background:linear-gradient(160deg,#eef3f7,#b9d6e6 45%,#dfe7ee)}
.p1 .kicker{top:366px;font-size:15px;color:var(--blue-deep);font-weight:300}
.p1 .question{top:386px;font-size:16px;color:var(--teal)}
.p1 .tag{top:406px;font-size:13px;color:var(--ink)}
/* poster 2 */
.greeting-cloud{position:absolute;left:18px;top:166px;width:298px;height:162px;
  background:linear-gradient(135deg,rgba(255,255,255,.28),rgba(255,255,255,.12) 55%,rgba(255,255,255,.22))}
.outline-box{position:absolute;left:42px;right:42px;top:362px;height:32px;border:1.5px solid #fff;color:#fff;
  text-align:center;line-height:29px;font-size:16px;font-family:"Montserrat",sans-serif;font-weight:500;letter-spacing:.5px}
/* poster 3 */
.bar{position:absolute;left:45px;width:254px;height:23px;color:#fff;text-align:center;line-height:23px;
  font-family:"Montserrat",sans-serif;font-size:12px;font-weight:500;white-space:nowrap}
.bar.t{background:var(--teal)}.bar.b{background:var(--blue)}
.p3 .photo{top:162px;bottom:0;background:linear-gradient(120deg,#d9e6f0,#eef2f5 40%,#c7a58c 70%,#9aa6b6)}
/* poster 4 */
.p4 .lead{top:114px;font-size:14px;color:var(--blue-deep);font-family:"Montserrat",sans-serif;font-weight:500}
.p4 .slab{position:absolute;left:16px;width:302px;top:134px;height:25px;background:var(--teal);color:#fff;
  text-align:center;line-height:25px;font-size:20px;white-space:nowrap}
.p4 .photo{top:178px;bottom:0;background:linear-gradient(180deg,#fff 0%,#f0e6dc 35%,#d9b79c 70%,#a9cfc6)}
/* poster 5 */
.p5 .title{top:101px;font-size:17px;color:var(--blue-deep);font-family:"Montserrat",sans-serif;font-weight:800;letter-spacing:.4px}
.p5 svg{position:absolute;left:0;top:0}
.price{position:absolute;left:198px;top:298px;width:112px;height:112px;border-radius:50%;display:flex;align-items:center;
  justify-content:center;text-align:center;color:#fff;font-family:"Montserrat",sans-serif;font-size:12px;line-height:1.35}
.price b{font-weight:700}
/* poster 6 */
.p6 svg.ribbon{position:absolute;left:18px;top:102px}
.p6 .ribbon-text{top:109px;font-size:12.5px;color:#fff;font-family:"Montserrat",sans-serif;font-weight:700}
.p6 .photo{top:131px;height:235px;background:linear-gradient(135deg,#f4f6f8,#dfe9f1 45%,#8cc6dc 75%,#e7eef3)}
.stats{position:absolute;left:0;right:0;top:366px;height:29px;display:flex}
.stats div{flex:1;color:#fff;text-align:center;line-height:29px;font-size:12px;font-family:"Oswald",sans-serif;font-weight:500;white-space:nowrap}
.stats .t{background:var(--teal-soft)}.stats .b{background:var(--sky)}
.p6 .answer{top:405px;font-size:14px;color:var(--teal);font-family:"Montserrat",sans-serif;font-weight:700}
</style>
</head>
<body>

<section class="poster p1">
  <div class="brand lg"><span class="dot"></span>CLINIVANTAGE LAB</div>
  <div class="photo" role="img" aria-label="Photo of a smiling dental assistant and a happy patient giving a thumbs up in the dental chair"></div>
  <p class="center kicker">BELANGRIJK TE WETEN</p>
  <p class="center cond question">Hoe de klant naar jouw praktijk kijkt?</p>
  <p class="center tag">WARME COMPLIMENTEN</p>
  <div class="band">Clinivantagelab.com</div>
</section>

<section class="poster p2">
  <div class="brand lg" style="top:105px;font-size:19px"><span class="dot"></span>CLINIVANTAGE LAB</div>
  <div class="greeting-cloud" role="img" aria-label="Word cloud of the word welcome in many languages, with welkom in large letters at the centre"></div>
  <div class="outline-box">WARME COMPLIMENTEN</div>
  <div class="band">Clinivantagelab.com</div>
</section>

<section class="poster p3">
  <div class="brand sm"><span class="dot"></span>CLINIVANTAGE LAB</div>
  <div class="bar t" style="top:81px">SCHITTERENDE RESULTATEN!</div>
  <div class="bar b" style="top:108px">BELANGRIJKE EN HELDERE FEEDBACK</div>
  <div class="bar t" style="top:135px">WARME COMPLIMENTEN</div>
  <div class="photo" role="img" aria-label="Photo of a smiling young woman in a dental practice"></div>
  <div class="band">Clinivantagelab.com</div>
</section>

<section class="poster p4">
  <div class="brand md"><span class="dot"></span>CLINIVANTAGE LAB</div>
  <p class="center lead">LAAT JE KLANTEN VERTELLEN</p>
  <div class="slab cond">Waar ze warm van worden!</div>
  <div class="photo" role="img" aria-label="Photo of a smiling senior couple embracing"></div>
  <div class="band">Clinivantagelab.com</div>
</section>

<section class="poster p5">
  <div class="brand sm" style="top:65px"><span class="dot"></span>CLINIVANTAGE LAB</div>
  <p class="center title">KLANTTEVREDENHEID METEN</p>
  <svg width="334" height="472" viewBox="0 0 334 472" aria-hidden="true">
    <circle cx="164" cy="274" r="142" fill="none" stroke="#2f8f7b" stroke-width="1.2"/>
  </svg>
  <svg width="334" height="472" viewBox="0 0 334 472" role="img" aria-label="Photo of a cheerful dental team with a laughing patient in the chair">
    <defs><linearGradient id="teamTone" x1="0" y1="0" x2="1" y2="1">
      <stop offset="0" stop-color="#cfe3ef"/><stop offset=".5" stop-color="#8fbcdc"/><stop offset="1" stop-color="#e8eef3"/></linearGradient></defs>
    <circle cx="164" cy="274" r="136" fill="url(#teamTone)"/>
  </svg>
  <div class="price" style="background:rgba(47,143,123,.9);box-shadow:0 0 0 2px #fff">
    <span>VOOR<br><b>SLECHTS €15</b><br>PER MAAND</span>
  </div>
  <div class="band">Clinivantagelab.com</div>
</section>

<section class="poster p6">
  <div class="brand sm" style="top:65px"><span class="dot"></span>CLINIVANTAGE LAB</div>
  <svg class="ribbon" width="300" height="29" viewBox="0 0 300 29" aria-hidden="true">
    <polygon points="12,0 288,0 300,29 0,29" fill="#2f8f7b"/>
  </svg>
  <p class="center ribbon-text">WAT IS HIER DE NET PROMOTER SCORE?</p>
  <div class="photo" role="img" aria-label="Photo of a person at a desk viewing a score dashboard on a computer monitor"></div>
  <div class="stats"><div class="t">105 PROMOTERS</div><div class="b">75 NEUTRALEN</div><div class="t">20 CRITICASTERS</div></div>
  <p class="center answer">VOOR HET ANTWOORD GA NAAR</p>
  <div class="band">Clinivantagelab.com</div>
</section>

</body>
</html>
```